Awsome new website

We are a Fencing Contracting company in Melbourne Australia. We supply and install Timer and Steel boundary fences as well as Pool fencing (e.g. glass, tubular steel). We also manufacture and install swing and sliding gates.

We want a new website that is a modern business website.
We are targeting domestic and business clients.
The design should compliment our logo and company name.
The website needs to be easy to update.

Some specifics we want.
Menu - Main menu at top of page and smaller footer menu (to add different menu items)
Slider - Main page to have a slider on it that's easy for us to add and remove slides.
Call to action - all pages to have a "call to action" logo or icon that attracts attention (see file "call_to_action.pdf)
Instant quote - we have a online quote page we need a distinctive logo or icon to redirect to this page.
Main page to have a product /Service guide (see file "website_idea.jpg")
Main page to have widgets or quick link to
o why choose us
o Brochures
o Gallery

Have a Gallery page formatted with different category galleries. e.g. Timber, Glass, Feature
Maintain the current link to our staff page with password, (link in footer menu)

Hopefully that covers everything.
Our current website is www.tallgumfencing.com.au to have a look at the current site.
regards Doug

• Turn off blogging as we don’t want 100’s of comments from spammers to delete

We would like to implement the Portalio plugin (see "http://portalio-plug.net/" ), but this can be done after the new Theme has been implemented.

```html
<!DOCTYPE html>
<html lang="en">
<head>
<meta charset="utf-8">
<title>Tall Gum Fencing</title>
<link href="https://fonts.googleapis.com/css2?family=Oswald:wght@400;500;700&family=Open+Sans:wght@400;600;700&family=Libre+Baskerville:ital@1&display=swap" rel="stylesheet">
<style>
:root{
  --red:#c1272d;
  --band:#ad2230;
  --ink:#333;
  --muted:#555;
  --grey-bg:#e6e6e6;
  --black:#000;
  --gold:#e9b521;
  --white:#fff;
}
*{box-sizing:border-box;margin:0;padding:0}
html,body{width:734px;height:1200px;overflow:hidden;background:#fff}
body{position:relative;font-family:"Open Sans",sans-serif;color:var(--ink)}
.abs{position:absolute}

.site-header{left:0;top:0;width:734px;height:101px;background:linear-gradient(#7d0f14,var(--red) 60%,#d32d33)}
.brand{left:80px;top:16px;width:200px;color:var(--white)}
.brand-name{display:flex;align-items:center;gap:5px;font-family:"Oswald",sans-serif;font-weight:700;font-size:18px;line-height:22px;white-space:nowrap}
.brand-name i{display:block;width:10px;height:10px;background:var(--white)}
.brand-tag{font-size:5.6px;font-weight:700;margin-top:4px;white-space:nowrap}
.phone{left:414px;top:21px;display:flex;align-items:center;gap:6px;color:var(--white);font-family:"Oswald",sans-serif;font-weight:500;font-size:15px}
.subscribe{left:520px;top:19px;width:134px;height:34px;background:var(--white);border-radius:17px 17px 0 17px;color:var(--red);font-family:"Oswald",sans-serif;font-weight:500;font-size:11px;display:flex;align-items:center;justify-content:center;padding-bottom:10px}
.main-nav{left:80px;top:65px;width:574px;height:27px;background:linear-gradient(#f7f7f7,#d9d9d9);border-radius:3px;display:flex;box-shadow:0 1px 2px rgba(0,0,0,.3)}
.main-nav a{flex:1;display:flex;align-items:center;justify-content:center;font-family:"Oswald",sans-serif;font-weight:500;font-size:11px;color:#333;text-decoration:none;border-right:1px solid #c8c8c8}
.main-nav a:last-child{border-right:0}
.main-nav a.current{color:var(--red)}

.slider{left:0;top:101px;width:734px;height:306px;background:linear-gradient(100deg,#d58d75,#c9734e 45%,#efe1cf 75%,#b9896a)}
.slide-arrow{top:142px;width:20px;height:20px;border-radius:50%;background:rgba(255,255,255,.75);display:flex;align-items:center;justify-content:center}

.services{left:0;top:407px;width:734px;height:126px;background:var(--band)}
.services-title{left:80px;top:11px;width:574px;display:flex;align-items:center;gap:10px;color:var(--white);font-family:"Oswald",sans-serif;font-weight:500;font-size:13px;justify-content:center}
.services-title::before,.services-title::after{content:"";width:180px;height:1px;background:rgba(255,255,255,.35)}
.service{top:38px;width:50px;text-align:center;color:var(--white);font-size:6.5px;line-height:10px}
.service span{display:block;width:44px;margin:0 auto}
.service-thumb{width:48px;height:48px;border:2px solid var(--white);margin:0 auto 8px}

.welcome-kicker{left:80px;top:555px;font-family:"Libre Baskerville",serif;font-style:italic;font-size:12px;color:#222}
.welcome-title{left:80px;top:567px;font-family:"Oswald",sans-serif;font-weight:500;font-size:15px;color:var(--red)}
.welcome-copy{left:80px;top:595px;width:378px;font-size:8px;line-height:13.3px;color:var(--muted)}
.read-more{left:80px;top:672px;font-size:7.5px;color:var(--red)}
.seal{left:502px;top:559px;width:110px;height:110px}
.seal-caption{left:462px;top:684px;width:190px;text-align:center;font-size:8.6px;font-weight:700;color:#111;white-space:nowrap}

.features{left:0;top:717px;width:734px;height:276px;background:var(--grey-bg)}
.feature{top:23px;width:180px}
.feature-img{width:180px;height:104px;border:3px solid var(--white);box-shadow:0 1px 3px rgba(0,0,0,.2)}
.feature h3{font-family:"Oswald",sans-serif;font-weight:500;font-size:14px;color:var(--red);margin-top:12px}
.feature p{font-size:8px;line-height:13.3px;color:var(--muted);margin-top:4px;height:56px;overflow:hidden}
.btn-pill{display:inline-block;margin-top:6px;padding:2px 11px;border:1px solid #c8c8c8;border-radius:8px;background:linear-gradient(#fff,#eee);font-size:7.5px;color:var(--red)}

.quote{left:292px;top:1017px;width:150px;height:47px;background:var(--band);border-radius:8px 8px 0 8px;display:flex;align-items:center;gap:10px;padding-left:16px;color:var(--white)}
.quote small{display:block;font-size:10px;line-height:10px}
.quote strong{display:block;font-family:"Oswald",sans-serif;font-weight:700;font-size:22px;line-height:22px}

.footer{left:0;top:1092px;width:734px;height:108px;background:var(--black)}
.footer h4{font-size:8.6px;font-weight:600;color:var(--white)}
.footer p{font-size:7.6px;color:#aaa;margin-top:6px}
.social{display:flex;gap:6px;margin-top:6px}
.social span{width:18px;height:18px;border-radius:50%;background:#777}
.copyright{left:0;top:83px;width:734px;text-align:center;font-size:7.5px;color:#aaa}
</style>
</head>
<body>

<header class="site-header abs">
  <div class="brand abs">
    <div class="brand-name"><i></i>Tall Gum Fencing</div>
    <div class="brand-tag">WHEN QUALITY COUNTS, COUNT ON US</div>
  </div>
  <div class="phone abs">
    <svg width="9" height="14" viewBox="0 0 9 14"><rect x="0.5" y="0.5" width="8" height="13" rx="1.5" fill="none" stroke="#fff"/><rect x="2" y="2.5" width="5" height="7" fill="#fff"/><circle cx="4.5" cy="11.5" r="0.9" fill="#fff"/></svg>
    03 9000 4127
  </div>
  <a class="subscribe abs">JOIN NOW SUBSCRIBE&nbsp;⊙</a>
  <nav class="main-nav abs">
    <a class="current">HOME</a><a>FENCES</a><a>GATES</a><a>DECKS</a><a>DIY</a><a>GALLERY</a><a>CONTACT US</a>
  </nav>
</header>

<section class="slider abs" role="img" aria-label="Slide photo: a couple working together on a home project">
  <span class="slide-arrow abs" style="left:80px"><svg width="8" height="10"><path d="M6 1L2 5l4 4" stroke="#999" stroke-width="1.6" fill="none"/></svg></span>
  <span class="slide-arrow abs" style="left:633px"><svg width="8" height="10"><path d="M2 1l4 4-4 4" stroke="#999" stroke-width="1.6" fill="none"/></svg></span>
</section>

<section class="services abs">
  <h2 class="services-title abs">OUR SERVICES</h2>
  <div class="service abs" style="left:79px"><div class="service-thumb" role="img" aria-label="Bathroom photo" style="background:linear-gradient(#d8c49a,#9a7a4e)"></div><span>Bathroom Remodeling</span></div>
  <div class="service abs" style="left:138px"><div class="service-thumb" role="img" aria-label="Attic photo" style="background:linear-gradient(#666,#222)"></div><span>Attic &amp; Garage Finishing</span></div>
  <div class="service abs" style="left:196px"><div class="service-thumb" role="img" aria-label="Carved wood photo" style="background:linear-gradient(#c58650,#7a4520)"></div><span>Carpentry</span></div>
  <div class="service abs" style="left:254px"><div class="service-thumb" role="img" aria-label="Tiled floor photo" style="background:linear-gradient(#9ec3dc,#4a7fa6)"></div><span style="width:34px">Tile &amp; Flooring</span></div>
  <div class="service abs" style="left:313px"><div class="service-thumb" role="img" aria-label="Deck photo" style="background:linear-gradient(#bfc8c0,#6b6b5a)"></div><span>Decks</span></div>
  <div class="service abs" style="left:371px"><div class="service-thumb" role="img" aria-label="Handyman photo" style="background:linear-gradient(#e4e4e4,#6f7f9a)"></div><span>General Home Maintenance</span></div>
  <div class="service abs" style="left:430px"><div class="service-thumb" role="img" aria-label="Painted wall photo" style="background:linear-gradient(#7c8a4a,#4a3b2a)"></div><span style="width:50px">Painting &amp; Wall Treatments</span></div>
  <div class="service abs" style="left:488px"><div class="service-thumb" role="img" aria-label="Drywall photo" style="background:linear-gradient(#cfcfcf,#8b8b8b)"></div><span style="width:30px">Drywall Install</span></div>
  <div class="service abs" style="left:546px"><div class="service-thumb" role="img" aria-label="Wiring photo" style="background:linear-gradient(#e0d2a8,#7b6f66)"></div><span>Electrical</span></div>
  <div class="service abs" style="left:604px"><div class="service-thumb" role="img" aria-label="Steel fence photo" style="background:linear-gradient(#7fb3e0,#1e2a3a)"></div><span>Fences</span></div>
</section>

<p class="welcome-kicker abs">Welcome to</p>
<h1 class="welcome-title abs">Tall Gum Fencing</h1>
<p class="welcome-copy abs">Thank you for visiting us at Tall Gum Fencing, my name is Doug and I am the Manager. I built my first fence when I was in my early twenties and have been building fences ever since. Over the last few years we have spent the time looking for fantastic fencing contractors to join our team. Because we only accept the best we have built our business to be one of Victoria's largest fencing contractors.</p>
<a class="read-more abs">Read More ›</a>
<div class="seal abs" role="img" aria-label="Quality seal" style="border-radius:50%;background:radial-gradient(circle,#f5d35a,#d9a21c 70%,#c28a12)"></div>
<p class="seal-caption abs">“When quality counts, Count on us”</p>

<section class="features abs">
  <article class="feature abs" style="left:80px">
    <div class="feature-img" role="img" aria-label="Family standing beside a white picket fence" style="background:linear-gradient(#b05a3a,#6d7b55 60%,#ddd)"></div>
    <h3>Why Choose Us</h3>
    <p>We offer a 12 month workman ship warranty on our fences and will clean the site for free of any fencing debris from the fence construction upon completion of the job...</p>
    <a class="btn-pill">Find Out More</a>
  </article>
  <article class="feature abs" style="left:277px">
    <div class="feature-img" role="img" aria-label="Fencing brochures laid over a garden fence photo" style="background:linear-gradient(#a8b8c8,#5d6a5a 60%,#c9a08a)"></div>
    <h3>Brochure</h3>
    <p>No pool is complete without a beautiful Pool fence. See our range of Tubular Fencing designs Download our Steelform Fencing Brochure and see what a fantastic...</p>
    <a class="btn-pill">Download Here</a>
  </article>
  <article class="feature abs" style="left:474px">
    <div class="feature-img" role="img" aria-label="House front with a black steel gate" style="background:linear-gradient(#cfe0ee,#c9b08a 45%,#4d5a3a)"></div>
    <h3>Gallery</h3>
    <p>Please feel free to look through our gallery, these are jobs that we have personally done! Please feel free to look through our gallery, these are jobs that we have personally ...</p>
    <a class="btn-pill">See Our Work</a>
  </article>
</section>

<a class="quote abs">
  <svg width="28" height="28" viewBox="0 0 28 28"><rect x="2" y="5" width="20" height="20" rx="3" fill="none" stroke="#fff" stroke-width="2.5"/><path d="M11 18l2-5 11-11 3 3-11 11z" fill="#fff"/></svg>
  <span><small>INSTANT</small><strong>QUOTE</strong></span>
</a>

<footer class="footer abs">
  <div class="abs" style="left:80px;top:34px"><h4>Quick Links</h4><p>Home &nbsp;|&nbsp; FAQ &nbsp;|&nbsp; Privacy &nbsp;|&nbsp; Staff</p></div>
  <div class="abs" style="left:326px;top:34px"><h4>Get In Touch</h4><p>Office : 03 9000 4127</p></div>
  <div class="abs" style="left:544px;top:34px"><h4>Stay Connect</h4><div class="social"><span></span><span></span><span></span><span></span></div></div>
  <p class="copyright abs">Copyright © 2013 Tall Gum Fencing.com.au</p>
</footer>

</body>
</html>
```